Harbour Lensman's Atlas for iOS

I am a keen travel and lifestyle photographer whose photographic studio is Velmora Imaging, based in Sydney, Australia. You can see my photographic portfolio at velmoraimaging.com.

Overview
-
I want to create an iOS app that will allow Sydney-bound photographers to develop an understanding of some the popular and lesser known sights of this beautiful city and its surrounds. I’d like to achieve this by making available to serious photographers information that will allow them plan their photographic expeditions and explore their own creative interpretations of some classic Sydney photographs. Aiding more serious photographers, the Harbour Lensman’s Atlas will include photographic metadata that most other photo sites exclude, allowing photographers to explore their own settings and creative options with guidance from scene-specific shooting data (Exposure and ISO settings, natural lighting and time of day, focal length etc).

The functionality of the iOS app I’d like to develop are:

1) Ability to review a thumbnail list of Sydney-based photographic galleries (Presented in a “Scenes” tab which the user starts with on launching the app).

a. A section at the bottom will include a “Sydney’s Surrounds” section which will be separated from the other Scenes by some kind of delimiter ( “………..” etc or something more stylish). Under this delimeter will be scenes from surround areas – including “The Hunter Valley”, “The Central Coast”, “The Blue Mountains”, “Woollongong”.

b. At the very bottom of app will be a “Link to Velmora Imaging by Tovin Marsell” which will link to the URL for my site.

2) Ability to select each ‘scene’ and be presented with a gallery of photograph thumbnails from this scene (Presented in a “Gallery” tab which is opened once a Scene is selected from within the “Scenes” tab by touching on that scene’s thumbnail or its associated brief). Note: You can use the “Gallery” drop down menu from my web site for a sense of how I’d like this to look.

3) Having selected a photograph’s thumbnail from the Gallery tab, a user is then taken to an “Image” screen that presents the photograph itself.

a. Within the Image screen, there will be an option to touch an “Info” button, selection of which will trigger the appearance of a semi-opaque overlay tile will appear with the following information:

i. Focal length:
ii. ISO:
iii. F-stop:
iv. Time:
v. Post-production:
vi. A general description field where information is provided around how the photograph was conceived and composed.

b. Within the Image screen, there also be a “Location” button”. On selecting “Location” the user will be taken to a “Map” screen that will present an iOS Maps screen with a pin showing the location the photograph was taken.

c. Finally, within the Image screen, there also be a “Favourite” button”. On selecting “Favourite” the user will ‘star’ the photo and it will be added to the Favourites screen accessed through the Favourites tab (see below)

4) Users will be presented with a fourth tab that will present the “Map” screen. It will be accessed by selecting the “Location” button from within the Image screen, or by directly pressing on the Maps tab itself. There will be Icon which if selected will pinpoint the user’s current location in relation to the photograph’s location (if one has been selected).

5) A “Favourites” screen will be accessed from a fifth Tab that will allow users to see a gallery of all their favourite photographs’ thumbnails.

General Navigation and Look and Feel
-
• I would like a clean and uncluttered modern design that takes guidance from the general look and feel of my website (velmoraimaging.com).
• The UI should be iPad and iPhone friendly. Note: The iPad version would be an expanded resolution of the iPhone version (ie. not relying on a 2x expansion but not necessarily requiring a whole new UI).

I'm looking forward to developing this concept further with your design involvement.
Updates

Hello

I have doubled the committed budget on this design.  Looking forward to your entries.  
Tovin

I do like the idea of a black backgrounded app.  This is the style of my site velmoraimaging.com and blends well into the photo styles used.  It is well presented in the initial design submitted.

Target Market(s)

Serious amateur and semi-pro photographers.

Industry/Entity Type

Travel

Requirements
Must have
• - Galleries that are tiled vertically. You can use the gearlodge app and its list of articles for a view of how this can be presented.

Basically, I'd like

Picture - brief description

You can get a sense of these by looking at my Gallery drop down menu from my website.

- The app needs to look like an app for pro users, and serious photographers. It's not intended to be gimicky, but look professional and elegant.
Should not have
• Not use old style fonts. I would like them clean and modern and economical.

```html
<!DOCTYPE html>
<html lang="en">
<head>
<meta charset="utf-8">
<title>Harbour Lensman's Atlas – Tab Bar</title>
<link rel="stylesheet" href="https://fonts.googleapis.com/css2?family=Oswald:wght@500&display=swap">
<style>
  :root {
    --page-bg: #ececec;
    --tab-top: #3b3b3b;
    --tab-bottom: #1f1f1f;
    --tab-edge: #151515;
    --tab-highlight: #5a5a5a;
    --active-top: #4a4a4a;
    --active-bottom: #2a2a2a;
    --active-highlight: #6a6a6a;
    --icon-light: #d6d6d6;
    --icon-dark: #9a9a9a;
    --label: #e4e4e4;
  }
  html, body {
    margin: 0;
    width: 1200px;
    height: 741px;
    overflow: hidden;
    background: var(--page-bg);
  }
  .tab-bar {
    position: absolute;
    left: 190px;
    top: 365px;
    width: 872px;
    height: 123px;
    display: flex;
    align-items: flex-end;
    gap: 2px;
  }
  .tab {
    height: 113px;
    box-sizing: border-box;
    border-radius: 12px 12px 0 0;
    background: linear-gradient(to bottom, var(--tab-top), var(--tab-bottom) 55%);
    border: 2px solid var(--tab-edge);
    border-bottom: none;
    box-shadow: inset 0 2px 0 var(--tab-highlight);
    display: flex;
    flex-direction: column;
    align-items: center;
    justify-content: flex-start;
    padding-top: 14px;
  }
  .tab--scenes { width: 158px; }
  .tab--gallery { width: 193px; }
  .tab--image { width: 158px; }
  .tab--map { width: 176px; }
  .tab--favorite { width: 179px; }
  .tab.is-active {
    height: 123px;
    background: linear-gradient(to bottom, var(--active-top), var(--active-bottom) 60%);
    box-shadow: inset 0 2px 0 var(--active-highlight), 0 -2px 8px rgba(0,0,0,0.35);
    padding-top: 16px;
  }
  .tab-icon {
    width: 70px;
    height: 56px;
    display: block;
  }
  .tab-icon--scenes {
    width: 92px;
    height: 50px;
    margin-top: 6px;
    background: linear-gradient(to bottom, var(--icon-light), var(--icon-dark));
    clip-path: polygon(0 100%, 10% 55%, 26% 20%, 38% 60%, 50% 10%, 64% 55%, 78% 25%, 90% 60%, 100% 100%);
  }
  .tab-label {
    margin-top: 8px;
    font-family: "Oswald", sans-serif;
    font-weight: 500;
    font-size: 15px;
    line-height: 18px;
    letter-spacing: 0.3px;
    text-transform: uppercase;
    color: var(--label);
    text-shadow: 0 1px 1px #000;
    white-space: nowrap;
  }
</style>
</head>
<body>
  <nav class="tab-bar" aria-label="Main tabs">
    <div class="tab tab--scenes">
      <div class="tab-icon tab-icon--scenes" role="img" aria-label="Scenes icon"></div>
      <span class="tab-label">Scenes</span>
    </div>

    <div class="tab tab--gallery is-active">
      <svg class="tab-icon" viewBox="0 0 70 56" aria-hidden="true">
        <defs>
          <linearGradient id="iconFill" x1="0" y1="0" x2="0" y2="1">
            <stop offset="0" stop-color="#d9d9d9"/>
            <stop offset="1" stop-color="#9a9a9a"/>
          </linearGradient>
        </defs>
        <rect x="8" y="10" width="54" height="40" rx="5" fill="url(#iconFill)"/>
        <rect x="24" y="4" width="22" height="10" rx="2" fill="url(#iconFill)"/>
        <circle cx="35" cy="31" r="13" fill="#3a3a3a"/>
        <circle cx="35" cy="31" r="9" fill="#c4c4c4"/>
        <circle cx="35" cy="31" r="5" fill="#555"/>
        <rect x="12" y="14" width="7" height="4" fill="#444"/>
      </svg>
      <span class="tab-label">Gallery</span>
    </div>

    <div class="tab tab--image">
      <svg class="tab-icon" viewBox="0 0 90 56" style="width:90px" aria-hidden="true">
        <defs>
          <linearGradient id="photoFill" x1="0" y1="0" x2="0" y2="1">
            <stop offset="0" stop-color="#cfcfcf"/>
            <stop offset="1" stop-color="#8f8f8f"/>
          </linearGradient>
        </defs>
        <g transform="rotate(-12 45 30)">
          <rect x="10" y="10" width="70" height="42" fill="url(#photoFill)"/>
          <rect x="14" y="14" width="62" height="34" fill="none" stroke="#6e6e6e" stroke-width="1.5" stroke-dasharray="3 2"/>
        </g>
      </svg>
      <span class="tab-label">Image</span>
    </div>

    <div class="tab tab--map">
      <svg class="tab-icon" viewBox="0 0 70 56" aria-hidden="true">
        <g fill="none" stroke="#c8c8c8" stroke-width="3">
          <circle cx="35" cy="28" r="25"/>
          <ellipse cx="35" cy="28" rx="11" ry="25"/>
          <line x1="35" y1="3" x2="35" y2="53"/>
          <line x1="10" y1="28" x2="60" y2="28"/>
          <path d="M14 15 H56 M14 41 H56"/>
        </g>
      </svg>
      <span class="tab-label">Map</span>
    </div>

    <div class="tab tab--favorite">
      <svg class="tab-icon" viewBox="0 0 70 56" aria-hidden="true">
        <defs>
          <linearGradient id="starFill" x1="0" y1="0" x2="0" y2="1">
            <stop offset="0" stop-color="#dcdcdc"/>
            <stop offset="1" stop-color="#9a9a9a"/>
          </linearGradient>
        </defs>
        <polygon points="35,2 42.5,20 62,21 47,34 52,53 35,43 18,53 23,34 8,21 27.5,20" fill="url(#starFill)"/>
      </svg>
      <span class="tab-label">Favorite</span>
    </div>
  </nav>
</body>
</html>
```